Harborline Lending and Capital. We provide MOSTLY residential home mortgages in Florida AND commercial loans for investment properties throughout the United states.
I would love to emulate so of the lender sites that are available on the internet but I would like to have the site as popular as possible for SEO purposes. Clients can already click the link to take them to the mortgage application where they can complete that and upload documents. If you could polish that up for me that would be great. I can also provide you with great detail on loan programs that are currently being offered. WE OFFER ALL MORTGAGE LENDING PRODUCTS. I would also like to add something in reference to the rate but I don't think it's legal to actually state or promise a rate for mortgage since they vary based on loan type, client and other criteria...

On the Harborline real estate site I would like to add a link or some way for clients to be able to put in credit card information to render services ...

Please let me know what you need from me

Thank you !!

Current link to site to improve and code

https://harborlinelendingandcapital.example/

Industry/Entity Type

Residential and commmercial lending

Coding

Coded - Design and coding required

Number of Pages Required

2 page

Requirements
Must have
• Love to integrate Mortgage interest rates even if general
Nice to have
• Link to fill out mortgage application via Quorvel LPX software

```html
<!DOCTYPE html>
<html lang="en">
<head>
<meta charset="utf-8">
<title>Harborline Lending and Capital</title>
<link href="https://fonts.googleapis.com/css2?family=Archivo:wght@300;400;600;700;800&family=Inter:wght@400;500;600;700&display=swap" rel="stylesheet">
<style>
:root{
  --dark:#1f3b1d;
  --lime:#8bc43f;
  --lime-soft:#e0f1d6;
  --ink:#1f2a1c;
  --muted:#5b6158;
  --line:#d6dad2;
  --white:#ffffff;
}
*{margin:0;padding:0;box-sizing:border-box}
html,body{width:1200px;height:5137px;overflow:hidden}
body{font-family:'Inter',sans-serif;color:var(--ink);background:var(--white);position:relative}
h1,h2,h3,.head{font-family:'Archivo',sans-serif}
.abs{position:absolute}
.btn{position:absolute;display:flex;align-items:center;justify-content:center;gap:8px;border-radius:30px;font-family:'Archivo',sans-serif;font-weight:700;font-size:13px;letter-spacing:.3px;text-transform:uppercase;color:var(--dark)}
.btn-fill{background:var(--lime)}
.btn-line{border:2px solid var(--dark);background:var(--white)}
.btn-line-lime{border:2px solid var(--lime);background:var(--white)}
.arrow{width:12px;height:10px}
.ph{position:absolute}
.underline{position:absolute;width:60px;height:9px}
.underline:before,.underline:after{content:"";position:absolute;left:0;height:3px;background:var(--lime);border-radius:2px}
.underline:before{top:0;width:60px}
.underline:after{top:6px;left:10px;width:40px}
.underline.dark:before,.underline.dark:after{background:var(--dark)}

/* top bar + nav */
.topbar{position:absolute;left:0;top:0;width:1200px;height:46px;background:var(--dark);color:var(--white);font-size:14px}
.topbar .item{position:absolute;top:14px;display:flex;align-items:center;gap:10px}
.social-dots{position:absolute;right:62px;top:16px;display:flex;gap:22px}
.social-dots span{width:12px;height:12px;border-radius:50%;background:var(--white)}
.social-dots span.on{background:var(--lime)}
.nav{position:absolute;left:0;top:46px;width:1200px;height:118px;background:var(--white)}
.brand{position:absolute;left:62px;top:40px;display:flex;align-items:center;gap:12px}
.brand .mark{width:34px;height:34px;background:var(--dark);border-radius:6px}
.brand .name{font-family:'Archivo',sans-serif;font-weight:700;font-size:13px;color:var(--dark);line-height:1.3;letter-spacing:.4px}
.menu{position:absolute;left:448px;top:50px;display:flex;gap:42px;font-family:'Archivo',sans-serif;font-weight:600;font-size:15px;color:var(--dark)}
.menu a{position:relative}
.menu a.active:after{content:"";position:absolute;left:10px;top:26px;width:24px;height:3px;background:var(--lime)}

/* hero */
.hero{position:absolute;left:0;top:164px;width:1200px;height:600px;background:var(--lime-soft)}
.hero h1{position:absolute;left:62px;top:150px;font-size:48px;line-height:54px;color:var(--dark);font-weight:800}
.hero h1 .light{font-weight:300}
.hero p{position:absolute;left:62px;top:334px;width:520px;font-size:20px;line-height:28px;color:var(--muted)}
.hero-mark{position:absolute;left:720px;top:40px;width:360px;height:360px;border-radius:50%;background:var(--dark);display:flex;align-items:center;justify-content:center}
.hero-mark span{font-family:'Archivo',sans-serif;font-weight:700;font-size:40px;color:var(--lime)}

/* about */
.about-photo{left:120px;top:828px;width:418px;height:460px;border-radius:22px;background:linear-gradient(160deg,#6e6a55,#2c3648 60%,#1d2a3d)}
.badge{position:absolute;left:64px;top:1044px;width:172px;height:214px;background:var(--lime);border-radius:60px 0 0 0;color:var(--dark);text-align:center}
.badge b{display:block;font-family:'Archivo',sans-serif;font-size:88px;font-weight:800;margin-top:30px;line-height:90px}
.badge small{display:block;font-family:'Archivo',sans-serif;font-weight:700;font-size:14px;line-height:22px}
.about h2{position:absolute;left:600px;top:820px;font-size:38px;line-height:44px;color:var(--dark);font-weight:800}
.about p{position:absolute;left:600px;top:944px;width:504px;font-size:15px;line-height:26px;color:var(--muted)}
.check{position:absolute;top:1092px;display:flex;align-items:center;gap:14px;font-size:15px;color:var(--ink)}
.check i{width:28px;height:28px;border-radius:50%;background:var(--dark);position:relative}
.check i:after{content:"";position:absolute;left:11px;top:9px;border-left:8px solid var(--white);border-top:5px solid transparent;border-bottom:5px solid transparent}
.divider{position:absolute;left:600px;top:1138px;width:504px;height:1px;background:var(--line)}
.call{position:absolute;left:790px;top:1172px;display:flex;align-items:center;gap:14px}
.call b{display:block;font-family:'Archivo',sans-serif;font-size:18px;font-weight:600;color:var(--dark)}
.call small{font-size:12px;color:var(--muted)}

/* services */
.services{position:absolute;left:0;top:1356px;width:1200px;height:906px;background:var(--dark)}
.section-title{position:absolute;left:0;width:1200px;text-align:center;font-size:38px;line-height:46px;font-weight:800}
.cards{position:absolute;left:64px;top:1648px;display:flex;gap:30px}
.card{width:338px;height:464px;background:var(--white);border-radius:12px;overflow:hidden;position:relative;text-align:center}
.card .img{height:258px}
.card h3{margin-top:28px;font-size:18px;font-weight:700;color:var(--dark)}
.card p{margin:14px auto 0;width:290px;font-size:15px;line-height:25px;color:var(--muted)}
.card .btn{left:88px;top:392px;width:162px;height:42px}

/* process */
.process-svg{position:absolute;left:190px;top:2392px}

/* properties */
.properties{position:absolute;left:0;top:2790px;width:1200px;height:720px;background:var(--lime)}
.properties h2{position:absolute;left:64px;top:2922px;font-size:38px;font-weight:800;color:var(--dark)}
.prop{position:absolute;top:3042px;width:248px;height:330px}
.prop .img{width:248px;height:290px;border-radius:12px}
.prop .label{position:absolute;left:0;top:250px;width:232px;height:80px;background:var(--white);border-radius:0 0 12px 12px;display:flex;align-items:center;justify-content:space-between;padding:0 18px 0 32px;font-family:'Archivo',sans-serif;font-weight:700;font-size:16px;line-height:20px;color:var(--dark)}
.plus{width:42px;height:42px;border-radius:50%;border:2px solid var(--lime);display:flex;align-items:center;justify-content:center;font-size:22px;font-weight:400;color:var(--dark)}
.plus.fill{background:var(--lime);border-color:var(--lime)}

/* calculator */
.calc-img{left:0;top:3540px;width:500px;height:440px;background:linear-gradient(180deg,#e8ece4,#c9ccc2)}
.rate-ring{position:absolute;left:128px;top:3600px;width:364px;height:364px;border-radius:50%;border:22px solid var(--lime);background:var(--white);text-align:center}
.rate-ring b{display:block;margin-top:142px;font-family:'Archivo',sans-serif;font-weight:800;font-size:52px;color:var(--dark)}
.rate-ring small{font-size:18px;color:var(--dark)}
.calc h2{position:absolute;left:598px;top:3556px;font-size:38px;font-weight:800;color:var(--dark)}
.calc p{position:absolute;left:598px;top:3634px;width:506px;font-size:15px;line-height:26px;color:var(--muted)}
.scale{position:absolute;left:598px;width:506px;display:flex;justify-content:space-between;font-size:15px;color:var(--muted)}
.track{position:absolute;left:598px;width:506px;height:3px;background:var(--line)}
.track .fill{position:absolute;left:0;top:0;height:3px;background:var(--lime)}
.track .knob{position:absolute;top:-8px;width:19px;height:19px;border-radius:50%;background:var(--white);border:4px solid var(--lime)}
.stat{position:absolute;top:3880px;display:flex;align-items:center;gap:12px}
.stat i{width:26px;height:24px;background:var(--dark);border-radius:4px}
.stat b{display:block;font-family:'Archivo',sans-serif;font-weight:700;font-size:19px;color:var(--dark)}
.stat small{font-size:12px;color:var(--muted)}

/* contact */
.contact{position:absolute;left:0;top:4050px;width:1200px;height:740px;background:var(--dark)}
.contact h2{position:absolute;left:62px;top:4172px;font-size:38px;font-weight:800;color:var(--white)}
.contact .lead{position:absolute;left:62px;top:4256px;font-size:15px;color:var(--white)}
.field{position:absolute;height:46px;background:var(--white);border-radius:3px;display:flex;align-items:center;gap:10px;padding-left:16px;font-size:15px;color:var(--muted)}
.field.area{align-items:flex-start;padding-top:16px}
.field i{width:14px;height:14px;background:var(--dark);border-radius:3px}
.person{left:604px;top:4216px;width:536px;height:520px;background:linear-gradient(180deg,#36503a,#7a7f7a 55%,#5b6468)}
.ball{position:absolute;left:960px;top:4276px;width:78px;height:78px;border-radius:50%;background:radial-gradient(circle at 35% 35%,#b9e27a,#6fa62a)}

/* footer */
.foot-brand{position:absolute;left:62px;top:4880px;display:flex;align-items:center;gap:12px}
.foot-brand .mark{width:40px;height:40px;border-radius:8px;background:var(--dark)}
.foot-brand .name{font-family:'Archivo',sans-serif;font-weight:700;font-size:20px;color:var(--dark);line-height:24px}
.foot-col{position:absolute;top:4830px}
.foot-col h4{font-family:'Archivo',sans-serif;font-size:17px;font-weight:700;color:var(--dark);margin-bottom:14px}
.foot-col li{list-style:none;font-size:15px;line-height:32px;color:var(--muted);display:flex;align-items:center;gap:10px}
.foot-col li i{width:12px;height:12px;border-radius:50%;background:var(--dark)}
.c-row{display:flex;align-items:center;gap:18px;font-size:15px;color:var(--muted);margin-bottom:22px}
.c-row i{width:54px;height:54px;border-radius:50%;background:var(--dark);display:flex;align-items:center;justify-content:center}
.copy{position:absolute;left:62px;top:5066px;width:1076px;border-top:1px solid var(--line);padding-top:32px;text-align:center;font-size:14px;color:var(--muted)}
</style>
</head>
<body>

<!-- top bar -->
<div class="topbar">
  <div class="item" style="left:62px">
    <svg width="14" height="14" viewBox="0 0 24 24"><path d="M6.6 10.8a15 15 0 0 0 6.6 6.6l2.2-2.2a1 1 0 0 1 1-.25 11.4 11.4 0 0 0 3.6.57 1 1 0 0 1 1 1V20a1 1 0 0 1-1 1A17 17 0 0 1 3 4a1 1 0 0 1 1-1h3.5a1 1 0 0 1 1 1c0 1.25.2 2.45.57 3.57a1 1 0 0 1-.25 1z" fill="#8bc43f"/></svg>
    (555) 014-2290
  </div>
  <div class="item" style="left:288px">
    <svg width="15" height="12" viewBox="0 0 24 18"><rect x="1" y="1" width="22" height="16" rx="2" fill="#8bc43f"/><path d="M2 2l10 8 10-8" stroke="#1f3b1d" stroke-width="2" fill="none"/></svg>
    info@harborlinelending.example
  </div>
  <div class="social-dots"><span></span><span class="on"></span><span></span><span></span></div>
</div>

<!-- nav -->
<header class="nav">
  <div class="brand"><span class="mark"></span><span class="name">HARBORLINE LENDING AND CAPITAL<br><span style="font-weight:400;font-size:10px;letter-spacing:1.6px">BUSINESS AND COMMERCIAL DIVISION</span></span></div>
  <nav class="menu"><a class="active">HOME</a><a>ABOUT US</a><a>OUR SERVICES</a><a>PROPERTIES</a></nav>
  <div class="btn btn-fill" style="left:974px;top:38px;width:162px;height:44px">Contact Us
    <svg class="arrow" viewBox="0 0 12 10"><path d="M1 5h9M6 1l4 4-4 4" stroke="#1f3b1d" stroke-width="1.8" fill="none"/></svg></div>
</header>

<!-- hero -->
<section class="hero">
  <h1><span class="light">Best Resource For</span><br>Hassle-free, Low Cost<br>Mortgage Origination</h1>
  <p>Residential home loans in florida and commercial lending in america</p>
  <div class="btn btn-fill" style="left:62px;top:420px;width:166px;height:46px">Get Started
    <svg class="arrow" viewBox="0 0 12 10"><path d="M1 5h9M6 1l4 4-4 4" stroke="#1f3b1d" stroke-width="1.8" fill="none"/></svg></div>
  <div class="hero-mark"><span>Harborline</span></div>
  <svg class="abs" style="left:0;top:530px" width="1200" height="70" viewBox="0 0 1200 70" preserveAspectRatio="none"><path d="M0 70 C 300 0, 900 0, 1200 70 Z" fill="#ffffff"/></svg>
</section>

<!-- about -->
<section class="about">
  <div class="ph about-photo" role="img" aria-label="Portrait of a smiling loan advisor in a suit and glasses"></div>
  <div class="badge"><b>25</b><small>YEARS OF<br>EXPERIENCE</small></div>
  <h2>About Harborline Lending<br>and Capital</h2>
  <div class="underline" style="left:600px;top:916px"></div>
  <p>Harborline Lending and Capital Originates Residential Home loans in Florida and Commercial and business financing in all 50 States. We have over 25 years of experience in ALL types of real estate and commercial lending.</p>
  <div class="check" style="left:600px"><i></i>We Target on Business</div>
  <div class="check" style="left:860px"><i></i>We Adapt Your Needs</div>
  <div class="divider"></div>
  <div class="btn btn-fill" style="left:600px;top:1170px;width:160px;height:46px">Learn More
    <svg class="arrow" viewBox="0 0 12 10"><path d="M1 5h9M6 1l4 4-4 4" stroke="#1f3b1d" stroke-width="1.8" fill="none"/></svg></div>
  <div class="call">
    <svg width="28" height="28" viewBox="0 0 24 24"><path d="M6.6 10.8a15 15 0 0 0 6.6 6.6l2.2-2.2a1 1 0 0 1 1-.25 11.4 11.4 0 0 0 3.6.57 1 1 0 0 1 1 1V20a1 1 0 0 1-1 1A17 17 0 0 1 3 4a1 1 0 0 1 1-1h3.5a1 1 0 0 1 1 1c0 1.25.2 2.45.57 3.57a1 1 0 0 1-.25 1z" fill="#1f3b1d"/></svg>
    <div><b>(555) 014-2290</b><small>Call us anytime</small></div>
  </div>
</section>

<!-- services -->
<section class="services">
  <svg class="abs" style="left:0;top:0" width="1200" height="70" viewBox="0 0 1200 70" preserveAspectRatio="none"><path d="M0 0 H1200 C 900 70, 300 70, 0 0 Z" fill="#ffffff"/></svg>
  <svg class="abs" style="left:0;top:836px" width="1200" height="70" viewBox="0 0 1200 70" preserveAspectRatio="none"><path d="M0 70 C 300 0, 900 0, 1200 70 Z" fill="#ffffff"/></svg>
</section>
<h2 class="section-title" style="top:1482px;color:#fff">We Pride Ourselves<br>On Offering Great Service</h2>
<div class="underline" style="left:570px;top:1586px"></div>
<div class="cards">
  <div class="card"><div class="img" role="img" aria-label="Agent handing house keys to a family outside a home" style="background:linear-gradient(180deg,#9cc3e4,#c9b8a3 60%,#6b8a4a)"></div>
    <h3>Residential Home Mortgages</h3><p>Ut enim ad minim veniam quis nostru dexercitation ullamco sed.</p>
    <div class="btn btn-line-lime"><span>Learn More</span><svg class="arrow" viewBox="0 0 12 10"><path d="M1 5h9M6 1l4 4-4 4" stroke="#1f3b1d" stroke-width="1.8" fill="none"/></svg></div></div>
  <div class="card"><div class="img" role="img" aria-label="Business team reviewing a tablet in a meeting" style="background:linear-gradient(180deg,#5a4a3a,#8a7a66 50%,#3a3e44)"></div>
    <h3>Professional Business Loan</h3><p>Ut enim ad minim veniam quis nostru dexercitation ullamco sed.</p>
    <div class="btn btn-fill"><span>Learn More</span><svg class="arrow" viewBox="0 0 12 10"><path d="M1 5h9M6 1l4 4-4 4" stroke="#1f3b1d" stroke-width="1.8" fill="none"/></svg></div></div>
  <div class="card"><div class="img" role="img" aria-label="Couple on a sofa reviewing investments on a laptop" style="background:linear-gradient(180deg,#e6e2dc,#a3b0bd 60%,#5d6b7c)"></div>
    <h3>Investment Properties Loan</h3><p>Ut enim ad minim veniam quis nostru dexercitation ullamco sed.</p>
    <div class="btn btn-line-lime"><span>Learn More</span><svg class="arrow" viewBox="0 0 12 10"><path d="M1 5h9M6 1l4 4-4 4" stroke="#1f3b1d" stroke-width="1.8" fill="none"/></svg></div></div>
</div>

<!-- process -->
<h2 class="section-title" style="top:2282px;color:var(--dark)">Our Working Process</h2>
<div class="underline" style="left:570px;top:2340px"></div>
<svg class="process-svg" width="820" height="370" viewBox="0 0 820 370" font-family="Archivo, sans-serif">
  <g fill="none" stroke="#1f3b1d" stroke-width="3">
    <path d="M280 10 H70 A66 66 0 0 0 70 142 H280"/>
    <path d="M540 10 H750 A66 66 0 0 1 750 142 H540"/>
    <path d="M280 218 H70 A66 66 0 0 0 70 350 H280"/>
    <path d="M540 218 H750 A66 66 0 0 1 750 350 H540"/>
    <path d="M340 140 C 340 180, 380 180, 410 180 C 440 180, 480 180, 480 140"/>
    <path d="M340 220 C 340 180, 380 180, 410 180 C 440 180, 480 180, 480 220"/>
    <path d="M368 76 C 400 80, 420 80, 452 76"/>
    <path d="M368 284 C 400 280, 420 280, 452 284"/>
  </g>
  <g stroke="#8bc43f" stroke-width="4" fill="#fff">
    <circle cx="306" cy="76" r="66"/><circle cx="514" cy="76" r="66"/>
    <circle cx="306" cy="284" r="66"/><circle cx="514" cy="284" r="66"/>
  </g>
  <g fill="none" stroke="#1f3b1d" stroke-width="2.5" stroke-linejoin="round">
    <rect x="286" y="52" width="36" height="46" rx="4"/><path d="M294 66h20M294 76h20M294 86h12M316 96l14-14 5 5-14 14h-5z"/>
    <rect x="490" y="58" width="48" height="38" rx="4"/><circle cx="504" cy="74" r="6"/><path d="M496 90c2-6 14-6 16 0M518 72h12M518 80h12"/><circle cx="536" cy="58" r="9"/><path d="M532 58l3 3 5-6"/>
    <circle cx="308" cy="266" r="13"/><path d="M308 259v14M303 263c0-3 10-3 10 0s-10 2-10 5 10 3 10 0"/><path d="M284 296h14l10 4h14l10-8v12l-14 6h-34z"/>
    <path d="M496 258h26l8 8v40h-34z"/><path d="M506 272h12M506 280h12M506 290h8"/><circle cx="530" cy="302" r="9"/><path d="M526 302l3 3 5-6"/>
  </g>
  <g fill="#1f3b1d">
    <text x="42" y="46" font-size="12" font-weight="700" letter-spacing="2">— STEP 1</text>
    <text x="42" y="70" font-size="18" font-weight="700">Application</text><text x="42" y="92" font-size="18" font-weight="700">Submit</text>
    <text x="622" y="46" font-size="12" font-weight="700" letter-spacing="2">— STEP 2</text>
    <text x="622" y="70" font-size="18" font-weight="700">Review and</text><text x="622" y="92" font-size="18" font-weight="700">Verification</text>
    <text x="42" y="254" font-size="12" font-weight="700" letter-spacing="2">— STEP 4</text>
    <text x="42" y="278" font-size="18" font-weight="700">Loan</text><text x="42" y="300" font-size="18" font-weight="700">Disbursement</text>
    <text x="622" y="254" font-size="12" font-weight="700" letter-spacing="2">— STEP 3</text>
    <text x="622" y="278" font-size="18" font-weight="700">Loan</text><text x="622" y="300" font-size="18" font-weight="700">Approval</text>
  </g>
</svg>

<!-- properties -->
<section class="properties">
  <svg class="abs" style="left:0;top:0" width="1200" height="70" viewBox="0 0 1200 70" preserveAspectRatio="none"><path d="M0 0 H1200 C 900 70, 300 70, 0 0 Z" fill="#ffffff"/></svg>
  <svg class="abs" style="left:0;top:650px" width="1200" height="70" viewBox="0 0 1200 70" preserveAspectRatio="none"><path d="M0 70 C 300 0, 900 0, 1200 70 Z" fill="#ffffff"/></svg>
</section>
<h2 class="properties" style="position:absolute;left:64px;top:2922px;width:auto;height:auto;background:none;font-size:38px;font-weight:800;color:var(--dark)">Available Properties</h2>
<div class="underline dark" style="left:64px;top:2978px"></div>
<div class="btn btn-line" style="left:976px;top:2930px;width:162px;height:46px;background:transparent">Learn More
  <svg class="arrow" viewBox="0 0 12 10"><path d="M1 5h9M6 1l4 4-4 4" stroke="#1f3b1d" stroke-width="1.8" fill="none"/></svg></div>
<div class="prop" style="left:64px"><div class="img" role="img" aria-label="Two-story suburban house with stone facade" style="background:linear-gradient(180deg,#9cc6ec,#c98a4a 55%,#7a7064)"></div>
  <div class="label"><span>14 Palmetto<br>Lane</span><span class="plus">+</span></div></div>
<div class="prop" style="left:340px"><div class="img" role="img" aria-label="Glass office tower against a blue sky" style="background:linear-gradient(180deg,#3f78c4,#8fb5e2 60%,#4a6b92)"></div>
  <div class="label"><span>38 Harbor<br>Avenue</span><span class="plus fill">+</span></div></div>
<div class="prop" style="left:616px"><div class="img" role="img" aria-label="Brick family home with tiled roof" style="background:linear-gradient(180deg,#b8cfe4,#b2714a 50%,#7a6a4a)"></div>
  <div class="label"><span>52 Seagrove<br>Street</span><span class="plus">+</span></div></div>
<div class="prop" style="left:892px"><div class="img" role="img" aria-label="Modern white villa with lawn" style="background:linear-gradient(180deg,#a9cdf0,#e7e7e4 55%,#6f9a4a)"></div>
  <div class="label"><span>76 Cypress<br>Boulevard</span><span class="plus">+</span></div></div>

<!-- calculator -->
<section class="calc">
  <div class="ph calc-img" role="img" aria-label="Two hands sheltering a rate badge"></div>
  <div class="rate-ring"><b>6.750%</b><small>Interest Rate</small></div>
  <h2>How Much Do You Need</h2>
  <div class="underline" style="left:598px;top:3608px"></div>
  <p>Lorem ipsum dolor sit amet consectetur adipisicing elit, sed do eiusmod tempor incididunt ut labore et dolore magna aliqua. Ut enim ad minim veniam reprehenderit.</p>
  <div class="scale" style="top:3732px"><span>$1,000</span><span>$25,000</span><span>$50,000</span></div>
  <div class="track" style="top:3770px"><div class="fill" style="width:254px"></div><div class="knob" style="left:244px"></div></div>
  <div class="scale" style="top:3802px"><span>1 month</span><span>6 month</span><span>24 month</span></div>
  <div class="track" style="top:3840px"><div class="fill" style="width:254px"></div><div class="knob" style="left:244px"></div></div>
  <div class="stat" style="left:598px"><i></i><div><b>$2200</b><small>Pay monthly</small></div></div>
  <div class="stat" style="left:786px"><i></i><div><b>6.750%</b><small>Interest rate</small></div></div>
  <div class="stat" style="left:972px"><i></i><div><b>$30,000</b><small>Total payable</small></div></div>
  <div class="btn btn-fill" style="left:598px;top:3948px;width:190px;height:46px">Apply For Loan
    <svg class="arrow" viewBox="0 0 12 10"><path d="M1 5h9M6 1l4 4-4 4" stroke="#1f3b1d" stroke-width="1.8" fill="none"/></svg></div>
  <div class="btn btn-line-lime" style="left:802px;top:3948px;width:198px;height:46px">Contact Us Now
    <svg class="arrow" viewBox="0 0 12 10"><path d="M1 5h9M6 1l4 4-4 4" stroke="#1f3b1d" stroke-width="1.8" fill="none"/></svg></div>
</section>

<!-- contact -->
<section class="contact">
  <svg class="abs" style="left:0;top:0" width="1200" height="70" viewBox="0 0 1200 70" preserveAspectRatio="none"><path d="M0 0 H1200 C 900 70, 300 70, 0 0 Z" fill="#ffffff"/></svg>
</section>
<div class="ph person" role="img" aria-label="Smiling agent in a checked blazer holding house keys and giving a thumbs up"></div>
<div class="ball"></div>
<svg class="abs" style="left:0;top:4720px" width="1200" height="70" viewBox="0 0 1200 70" preserveAspectRatio="none"><path d="M0 70 C 300 0, 900 0, 1200 70 Z" fill="#ffffff"/></svg>
<h2 class="contact" style="position:absolute;left:62px;top:4172px;width:auto;height:auto;background:none;font-size:38px;font-weight:800;color:#fff">Get in Touch</h2>
<div class="underline" style="left:62px;top:4226px"></div>
<p class="lead" style="position:absolute;left:62px;top:4256px;font-size:15px;color:#fff">Please send me a message for general inquiries or reservations.</p>
<div class="field" style="left:62px;top:4316px;width:258px"><i></i>First Name</div>
<div class="field" style="left:338px;top:4316px;width:258px"><i></i>Last Name</div>
<div class="field" style="left:62px;top:4382px;width:258px"><i></i>Email Address</div>
<div class="field" style="left:338px;top:4382px;width:258px"><i></i>Phone</div>
<div class="field area" style="left:62px;top:4448px;width:534px;height:140px"><i></i>Leave your message...</div>
<div class="btn btn-fill" style="left:62px;top:4612px;width:182px;height:46px">Send Message
  <svg class="arrow" viewBox="0 0 12 10"><path d="M1 5h9M6 1l4 4-4 4" stroke="#1f3b1d" stroke-width="1.8" fill="none"/></svg></div>

<!-- footer -->
<footer>
  <div class="foot-brand"><span class="mark"></span><span class="name">Harborline</span></div>
  <div class="foot-col" style="left:326px"><h4>Quick Links</h4><ul><li>Home</li><li>About Us</li><li>Our Services</li><li>Properties</li></ul></div>
  <div class="foot-col" style="left:582px"><h4>Contact Information</h4>
    <div class="c-row"><i><svg width="18" height="14" viewBox="0 0 24 18"><rect x="1" y="1" width="22" height="16" rx="2" fill="#8bc43f"/><path d="M2 2l10 8 10-8" stroke="#1f3b1d" stroke-width="2" fill="none"/></svg></i>info@harborline.example</div>
    <div class="c-row"><i><svg width="18" height="18" viewBox="0 0 24 24"><path d="M6.6 10.8a15 15 0 0 0 6.6 6.6l2.2-2.2a1 1 0 0 1 1-.25 11.4 11.4 0 0 0 3.6.57 1 1 0 0 1 1 1V20a1 1 0 0 1-1 1A17 17 0 0 1 3 4a1 1 0 0 1 1-1h3.5a1 1 0 0 1 1 1c0 1.25.2 2.45.57 3.57a1 1 0 0 1-.25 1z" fill="#8bc43f"/></svg></i>(555) 014-2290</div>
  </div>
  <div class="foot-col" style="left:1026px"><h4>Social Links</h4><ul><li><i></i>Community</li><li><i></i>Updates</li><li><i></i>Videos</li><li><i></i>Gallery</li></ul></div>
  <div class="copy">Copyright © 2025 Harborline Lending and Capital Of Florida. All rights reserved.</div>
</footer>

</body>
</html>
```